Homepage layout for online ad network

Attached is our Valtro Media logo and updated brief (I can't seem to delete the old logo and brief, but they're no longer relevant).

This project was originally posted with a different logo and corporate name, but we have decided to stay with our current logo and name and redesign the site.

Your design is for a homepage only - design, no coding (I'll get someone else to take your PSD and code it).

Your homepage will make use of a Flash slider - BUT YOU ARE NOT REQUIRED TO PROVIDE THE FLASH. Instead, simply provide the layout and at least two static examples out of the four different sections that will eventually be in the slider.

Much of this design is based on the design of a competitor (listed in the brief).

Please ask whatever questions you need to in order to clarify instructions.
Updates

Project updated to include new logo (and correspondingly new color scheme).

Brief changed slightly.

Thank you for submitting designs for this project in the past.

After some internal strategy work, we have decided to retain our initial corporate identity, Valtro Media.

If you have submitted a design for the original brief and are available, please re-work your best prior design to reflect the color scheme in the newly uploaded logo.

Target Market(s)

This site is aimed primarily at young professionals who buy digital media on behalf of large advertisers.

Industry/Entity Type

Media

Requirements
Must have
• modern white space
Should not have
• no Flash outside of slider

```html
<!DOCTYPE html>
<html lang="en">
<head>
<meta charset="utf-8">
<title>Valtro Media — Home</title>
<link href="https://fonts.googleapis.com/css2?family=Arimo:ital,wght@0,400;0,700;1,400&display=swap" rel="stylesheet">
<style>
:root{
  --brand-red:#c0282e;
  --ink:#2c2c2c;
  --band-top:#5d6470;
  --band-mid:#3a404a;
  --band-low:#1f242b;
  --card:#3c4668;
  --card-top:#56618a;
  --card-edge:#c9ccd4;
  --btn-top:#e9effa;
  --btn-low:#b3c4e3;
  --btn-ink:#1d2a4a;
  --arrow:#4f78c4;
  --news-ink:#2f3a5c;
  --rule:#8a8f99;
  --white:#ffffff;
}
*{margin:0;padding:0;box-sizing:border-box}
html,body{width:1200px;height:900px;overflow:hidden;background:var(--white);font-family:"Arimo",Arial,sans-serif;color:var(--ink)}
.page{position:relative;width:1200px;height:900px;background:linear-gradient(#fff 0,#fff 385px,#eef0f3 420px,#fff 560px)}
.header{position:absolute;left:0;top:0;width:1200px;height:92px;background:linear-gradient(#fff 0,#f3f3f4 60%,#e2e3e6 100%)}
.brand{position:absolute;left:216px;top:30px;display:flex;align-items:center;gap:10px}
.brand-mark{width:14px;height:14px;background:var(--brand-red)}
.brand-name{font-size:26px;font-weight:400;color:var(--ink)}
.band{position:absolute;left:0;width:1200px;background:linear-gradient(var(--band-top),var(--band-mid) 55%,var(--band-low))}
.band-top{top:92px;height:30px}
.band-bottom{top:352px;height:31px}
.main-nav{position:absolute;right:214px;top:8px;display:flex;gap:7px;font-size:12px;font-weight:700;color:var(--white)}
.main-nav span.sep{font-weight:400}
.slider{position:absolute;left:0;top:122px;width:1200px;height:230px;background:#000}
.slide{position:absolute;left:193px;top:0;width:806px;height:230px;background:var(--white)}
.slide-dot{position:absolute;left:388px;top:98px;width:24px;height:24px;border-radius:50%;background:#000}
.card{position:absolute;top:409px;width:186px;height:181px;border-radius:9px;border:3px solid var(--card-edge);background:linear-gradient(var(--card-top),var(--card) 40px);box-shadow:0 3px 6px rgba(0,0,0,.35);color:var(--white);overflow:hidden}
.card h2{position:absolute;left:16px;top:13px;font-size:17px;font-weight:700}
.card p{position:absolute;left:16px;top:42px;width:160px;font-size:10.5px;line-height:12px}
.card-photo{position:absolute;left:1px;top:82px;width:178px;height:51px}
.btn{position:absolute;left:42px;top:145px;width:102px;height:23px;border-radius:12px;background:linear-gradient(var(--btn-top),var(--btn-low));color:var(--btn-ink);font-size:12px;line-height:23px;padding-left:9px}
.btn svg{position:absolute;right:7px;top:6px}
.news{position:absolute;left:193px;top:618px;width:604px;height:127px;border-radius:12px;border:4px solid #b9bdc6;background:linear-gradient(#fdfdfd,#f2f3f6);box-shadow:0 3px 6px rgba(0,0,0,.3)}
.news-label{position:absolute;left:22px;top:8px;width:28px;font-size:27px;line-height:27px;font-weight:400;font-style:italic;color:#9aa0ab;text-align:center}
.news-rule{position:absolute;left:66px;top:8px;width:1px;height:108px;background:var(--rule)}
.news-list{position:absolute;left:85px;top:9px;list-style:none;font-size:10.5px;color:var(--news-ink)}
.news-list time{display:block;font-style:italic;height:18px}
.news-list span{display:block;height:17px}
.news-up{position:absolute;right:12px;top:9px}
.news-down{position:absolute;right:12px;top:97px}
.footer-nav{position:absolute;left:449px;top:776px;font-size:9.5px;color:#333;word-spacing:1px}
.copyright{position:absolute;left:518px;top:798px;font-size:7.5px;color:#333;letter-spacing:.6px}
</style>
</head>
<body>
<div class="page">
  <header class="header">
    <div class="brand"><span class="brand-mark"></span><span class="brand-name">Valtro Media</span></div>
  </header>

  <div class="band band-top">
    <nav class="main-nav"><span>Beauty</span><span class="sep">|</span><span>Cooking</span><span class="sep">|</span><span>Parenting</span><span class="sep">|</span><span>Video</span></nav>
  </div>

  <section class="slider">
    <div class="slide"><span class="slide-dot"></span></div>
  </section>

  <div class="band band-bottom"></div>

  <article class="card" style="left:193px">
    <h2>Lorem ipsum</h2>
    <p>Lorem ipsum dolor sit amet, consecteturo eiusmod tempor incididunt ut labolore magna.</p>
    <div class="card-photo" role="img" aria-label="Black and white beauty portrait" style="background:linear-gradient(90deg,#5a5a5a,#d8d8d8 50%,#6b6b6b)"></div>
    <a class="btn">Read more<svg width="10" height="12" viewBox="0 0 10 12"><path d="M2 1l6 5-6 5" fill="none" stroke="var(--arrow)" stroke-width="2.4"/></svg></a>
  </article>
  <article class="card" style="left:400px">
    <h2>Lorem ipsum</h2>
    <p>Lorem ipsum dolor sit amet, consecteturo eiusmod tempor incididunt ut labolore magna.</p>
    <div class="card-photo" role="img" aria-label="Cooking scene with vegetables being chopped" style="background:linear-gradient(90deg,#6b4a2e,#c9a889 45%,#d28a2a 80%,#e0b83a)"></div>
    <a class="btn">Read more<svg width="10" height="12" viewBox="0 0 10 12"><path d="M2 1l6 5-6 5" fill="none" stroke="var(--arrow)" stroke-width="2.4"/></svg></a>
  </article>
  <article class="card" style="left:607px">
    <h2>Lorem ipsum</h2>
    <p>Lorem ipsum dolor sit amet, consecteturo eiusmod tempor incididunt ut labolore magna.</p>
    <div class="card-photo" role="img" aria-label="Black and white parenting photo" style="background:linear-gradient(90deg,#8a8a8a,#e4e4e4 50%,#707070)"></div>
    <a class="btn">Read more<svg width="10" height="12" viewBox="0 0 10 12"><path d="M2 1l6 5-6 5" fill="none" stroke="var(--arrow)" stroke-width="2.4"/></svg></a>
  </article>
  <article class="card" style="left:812px">
    <h2>Lorem ipsum</h2>
    <p>Lorem ipsum dolor sit amet, consecteturo eiusmod tempor incididunt ut labolore magna.</p>
    <div class="card-photo" role="img" aria-label="Video production clapperboard scene" style="background:linear-gradient(90deg,#1e1e1e,#6a6a6a 45%,#bdbdbd 75%,#3a3a3a)"></div>
    <a class="btn">Read more<svg width="10" height="12" viewBox="0 0 10 12"><path d="M2 1l6 5-6 5" fill="none" stroke="var(--arrow)" stroke-width="2.4"/></svg></a>
  </article>

  <section class="news">
    <div class="news-label">N E W S</div>
    <div class="news-rule"></div>
    <ul class="news-list">
      <li><time>September 29, 2010</time><span>Lorem ipsum dolor sit amet, consectetur adipiscing elit. Aenean vulputate ultrices mauris vitae lacinia</span></li>
      <li><time>September 24, 2010</time><span>Lorem ipsum dolor sit amet, consectetur adipiscing elit. Aenean vulputate ultrices mauris vitae lacinia</span></li>
      <li><time>September 24, 2010</time><span>Lorem ipsum dolor sit amet, consectetur adipiscing elit. Aenean vulputate ultrices mauris vitae lacinia</span></li>
    </ul>
    <svg class="news-up" width="16" height="12" viewBox="0 0 16 12"><path d="M2 10l6-7 6 7" fill="none" stroke="var(--arrow)" stroke-width="3"/></svg>
    <svg class="news-down" width="16" height="12" viewBox="0 0 16 12"><path d="M2 2l6 7 6-7" fill="none" stroke="var(--arrow)" stroke-width="3"/></svg>
  </section>

  <nav class="footer-nav">About us &nbsp;| &nbsp;Contact Us &nbsp;| &nbsp;Management Team &nbsp;| &nbsp;News &nbsp;| &nbsp;Careers</nav>
  <p class="copyright">Copyright ©2010</p>
</div>
</body>
</html>
```